Kelvara Pane Works Business Card

We need a business card design that is suitable for a Glazing Business. We Specialize in Repairing broken windows and doors and are a 24hr on call service. We manufacture Shower screens, Fly screens, Wardrobe doors, Security doors and grilles + mirrors. We stock a variety of mesh including Standard mesh, Pet resistant mesh, Tressmet & Clearweft. We would like to use a combination of Light Blue, Dark Blue, Black & White with perhaps a picture of glass breaking.

Industry/Entity Type

Business

Contact Information for Business Card

Narooma Glass Service60B Glasshouse Rocks RdNarooma NSW 2546PH / FAX - 02 44765210MOB - 0419682350 Andrewemail - kelvarapane@fenmail.example

Font styles to use
Serif

Colors
34a7d8
0255a3
ffffff

Requirements
Must have
• logo with picture of broken or cracked glass

```html
<!DOCTYPE html>
<html lang="en">
<head>
<meta charset="utf-8">
<title>Kelvara Pane Works – Business Card</title>
<link href="https://fonts.googleapis.com/css2?family=Lato:wght@400;700&display=swap" rel="stylesheet">
<style>
  :root {
    --stage: #000000;
    --card: #333539;
    --rule: #45474b;
    --brand-blue: #1f63dc;
    --light-blue: #34a7d8;
    --deep-blue: #0255a3;
    --text: #ffffff;
  }
  html, body {
    margin: 0;
    width: 1200px;
    height: 900px;
    overflow: hidden;
    background: var(--stage);
    font-family: "Lato", Arial, sans-serif;
    color: var(--text);
  }
  .stage { position: relative; width: 1200px; height: 900px; }
  .card {
    position: absolute;
    top: 271px;
    width: 457px;
    height: 281px;
    border-radius: 14px;
    background: var(--card);
  }
  .card--front { left: 137px; }
  .card--back { left: 626px; }

  .brand-tile {
    position: absolute;
    left: 49px; top: 76px;
    width: 130px; height: 130px;
    border: 2px solid #e8eef4;
    background: linear-gradient(135deg, #bfe3f5, var(--light-blue) 55%, var(--deep-blue));
    display: flex; align-items: center; justify-content: center;
    text-align: center;
  }
  .brand-tile__name {
    font-size: 17px; font-weight: 700; line-height: 1.2;
    color: var(--text); padding: 0 10px;
  }
  .divider {
    position: absolute; left: 210px; top: 80px;
    width: 1px; height: 130px; background: var(--rule);
  }
  .contact { position: absolute; left: 242px; top: 60px; }
  .contact__name {
    margin: 0 0 14px; font-size: 17px; font-weight: 700; color: var(--brand-blue);
  }
  .contact__address { margin: 0 0 14px; font-size: 13px; line-height: 19px; }
  .contact__list { list-style: none; margin: 0; padding: 0; font-size: 13px; }
  .contact__list li { display: flex; align-items: center; height: 19.5px; }
  .contact__list svg { width: 10px; height: 10px; margin-right: 5px; fill: var(--brand-blue); }

  .wordmark {
    position: absolute; left: 44px; top: 40px;
    display: flex; align-items: center;
  }
  .wordmark__square {
    width: 64px; height: 64px; margin-right: 8px;
    background: linear-gradient(135deg, #bfe3f5, var(--light-blue) 55%, var(--deep-blue));
  }
  .wordmark__text {
    font-weight: 400; color: var(--brand-blue); line-height: 1;
  }
  .wordmark__top { display: block; font-size: 42px; letter-spacing: 1px; }
  .wordmark__bottom { display: block; font-size: 24px; letter-spacing: 3.5px; margin-top: 4px; }

  .services {
    position: absolute; left: 118px; top: 151px;
    list-style: none; margin: 0; padding: 0;
    font-size: 13px; font-weight: 700;
  }
  .services li { position: relative; padding-left: 14px; height: 20.5px; line-height: 20.5px; }
  .services li::before {
    content: ""; position: absolute; left: 0; top: 7px;
    width: 6px; height: 6px; border-radius: 50%; background: var(--brand-blue);
  }
</style>
</head>
<body>
<main class="stage">
  <section class="card card--front">
    <div class="brand-tile" role="img" aria-label="Kelvara Pane Works brand tile">
      <span class="brand-tile__name">Kelvara Pane Works</span>
    </div>
    <div class="divider"></div>
    <div class="contact">
      <h2 class="contact__name">Malcolm</h2>
      <p class="contact__address">17C Tindale Ridge<br>RdKelvara NSW 2591</p>
      <ul class="contact__list">
        <li><svg viewBox="0 0 10 10"><path d="M2 0.5 L3.6 2.6 L2.8 3.6 Q4 6 6.4 7.2 L7.4 6.4 L9.5 8 L8.2 9.5 Q4.5 9.2 0.5 1.8 Z"/></svg>02 48931067</li>
        <li><svg viewBox="0 0 10 10"><rect x="2.5" y="0.5" width="5" height="3"/><rect x="0.5" y="3.5" width="9" height="5" rx="1"/></svg>02 48931067</li>
        <li><svg viewBox="0 0 10 10"><path d="M2.5 0h5a1 1 0 0 1 1 1v8a1 1 0 0 1-1 1h-5a1 1 0 0 1-1-1V1a1 1 0 0 1 1-1zM3 1.5v6h4v-6z"/></svg>0419682350</li>
        <li><svg viewBox="0 0 10 10"><path d="M0.5 2h9v6h-9z M0.5 2 L5 5.5 L9.5 2" stroke="#333539" stroke-width="0.8"/></svg>kelvarapane@fenmail.example</li>
      </ul>
    </div>
  </section>

  <section class="card card--back">
    <div class="wordmark">
      <div class="wordmark__square"></div>
      <div class="wordmark__text">
        <span class="wordmark__top">KELVARA</span>
        <span class="wordmark__bottom">PANE WORKS</span>
      </div>
    </div>
    <ul class="services">
      <li>Shower screens</li>
      <li>Fly screens</li>
      <li>Wardrobe doors</li>
      <li>Security doors</li>
      <li>Grilles + mirrors</li>
    </ul>
  </section>
</main>
</body>
</html>
```